Redesign of business card for Cedar Ridge Mechanical

We are looking for a new design for our business cards for Cedar Ridge Mechanical. We are a plumbing & HVAC construction company, operating on the West Coast of Canada and USA. Logo attached.
Industry/Entity Type
Construction - Plumbing & HVAC
Contact Information for Business Card
Name, address, phone numbers, email, website address
Look and feel
Each slider illustrates characteristics of the customer's brand and the style your logo design should communicate.

```html
<!DOCTYPE html>
<html lang="en">
<head>
<meta charset="utf-8">
<title>Cedar Ridge Mechanical – Business Card</title>
<link rel="stylesheet" href="https://fonts.googleapis.com/css2?family=Montserrat:wght@300;700&family=Lato:wght@400&display=swap">
<style>
  :root {
    --bg: #e9e7e4;
    --card-dark: #1b1b1b;
    --card-light: #ffffff;
    --ink: #111111;
    --ink-mid: #3a3a3a;
    --ink-soft: #555555;
    --mark-dark: #2c2c2c;
    --divider: #6a6a6a;
  }
  * { box-sizing: border-box; margin: 0; padding: 0; }
  html, body {
    width: 1200px;
    height: 900px;
    overflow: hidden;
    background: var(--bg);
  }
  .canvas {
    width: 1200px;
    height: 900px;
    display: flex;
    flex-direction: column;
    align-items: center;
    justify-content: center;
    gap: 40px;
  }
  .card {
    width: 640px;
    height: 366px;
    box-shadow: 0 6px 18px rgba(0,0,0,0.18);
    position: relative;
  }
  .card--back {
    background: var(--card-dark);
    display: flex;
    align-items: center;
    justify-content: center;
  }
  .brand {
    display: flex;
    align-items: center;
    gap: 12px;
    font-family: "Montserrat", sans-serif;
    font-weight: 700;
    text-transform: uppercase;
    letter-spacing: 0.04em;
    white-space: nowrap;
  }
  .brand__square {
    width: 18px;
    height: 18px;
    flex: none;
  }
  .card--back .brand { color: var(--mark-dark); font-size: 26px; }
  .card--back .brand__square { background: var(--mark-dark); }

  .card--front {
    background: var(--card-light);
    display: flex;
    align-items: center;
  }
  .front__brand-area {
    width: 330px;
    padding: 0 14px;
    display: flex;
    justify-content: center;
  }
  .card--front .brand { color: var(--ink-mid); font-size: 16px; gap: 10px; }
  .card--front .brand__square { background: var(--ink-mid); width: 13px; height: 13px; }
  .divider {
    width: 1px;
    height: 150px;
    background: var(--divider);
    flex: none;
  }
  .contact {
    padding-left: 30px;
    color: var(--ink);
  }
  .contact__name {
    font-family: "Montserrat", sans-serif;
    font-weight: 700;
    font-size: 25px;
    letter-spacing: 0.02em;
    line-height: 1.05;
  }
  .contact__title {
    font-family: "Montserrat", sans-serif;
    font-weight: 300;
    font-size: 15px;
    letter-spacing: 0.04em;
    color: var(--ink-soft);
    margin-bottom: 16px;
  }
  .contact__list { list-style: none; }
  .contact__item {
    display: flex;
    align-items: center;
    gap: 10px;
    font-family: "Lato", sans-serif;
    font-size: 15px;
    line-height: 1.35;
  }
  .contact__item svg { width: 13px; height: 13px; flex: none; fill: var(--ink); }
  .contact__address {
    font-family: "Lato", sans-serif;
    font-size: 15px;
    line-height: 1.3;
    margin-top: 10px;
  }
</style>
</head>
<body>
<main class="canvas">
  <section class="card card--back" aria-label="Card back">
    <div class="brand"><span class="brand__square"></span>Cedar Ridge Mechanical</div>
  </section>

  <section class="card card--front" aria-label="Card front">
    <div class="front__brand-area">
      <div class="brand"><span class="brand__square"></span>Cedar Ridge Mechanical</div>
    </div>
    <div class="divider"></div>
    <div class="contact">
      <h1 class="contact__name">MARCUS REED</h1>
      <p class="contact__title">MANAGING DIRECTOR</p>
      <ul class="contact__list">
        <li class="contact__item">
          <svg viewBox="0 0 24 24" aria-hidden="true"><path d="M6.6 10.8a15.1 15.1 0 0 0 6.6 6.6l2.2-2.2c.3-.3.7-.4 1-.2 1.1.4 2.3.6 3.6.6.6 0 1 .4 1 1V20c0 .6-.4 1-1 1A17 17 0 0 1 3 4c0-.6.4-1 1-1h3.5c.6 0 1 .4 1 1 0 1.3.2 2.5.6 3.6.1.3 0 .7-.2 1z"/></svg>
          604-555 210 388
        </li>
        <li class="contact__item">
          <svg viewBox="0 0 24 24" aria-hidden="true"><path d="M2 5h20v14H2zM2 6l10 7 10-7v2l-10 7L2 8z"/></svg>
          info@crmech.com
        </li>
        <li class="contact__item">
          <svg viewBox="0 0 24 24" aria-hidden="true"><circle cx="12" cy="12" r="10"/></svg>
          www.cedarridgemech.com
        </li>
      </ul>
      <p class="contact__address">318, Harbour Crescent Road<br>V6B 2K4, Canada</p>
    </div>
  </section>
</main>
</body>
</html>
```